Law Firm Web Design Project

I need a website design for my law firm. I have attached to this description the URL of a website I liked with a description of the elements of that website that appeal to me.

I am also attaching my law firm's logo, so you can review that design when you create the website design.

Reference Site: www.harborfieldcounsel-example.com

What we like about this site:
• The different layers
• Subtle designs, textures, curves
• 3 dimensional
• Floating effect
• Simple logo that stands out (we are providing logo)
• Prominent phone number
• Location of Areas of Practice
oDivorce, Legal Separation, Paternity, Spousal Maintenance, Child Custody, Child Support, Protective Orders, Community Property, Business Evaluations
• The limited amount of links across the top
o Home, Meet Our Attorney, FAQ, Contact Us
• Request A Consultation click through
• Right side bar with the moving icons
• Badges

Other Tips:
• We don’t want the website to be dark. The logo can standout and the website can have its own colors and flow.
• We would like there to be a “call to action” or way to get in touch on every page and every page view
• We would like a place for credit card icons at the bottom of the page
• Strong, yet elegant
• Finally, just use the website provided as a guide. Explore different colors, textures, shapes, shadows etc.
Updates

I would prefer the website have colors that are complementary to my logo and that are strong and elegant.  I like black, gold, amber, and tan colors.  Black should be used sparingly as an accent only, since I don't want the website to be too dark.

Please review the website I provided as an example in my project description.  I really like the three dimensional aspects of that website (web page floating on top of a background and the logo in the upper left floating on top of the web page).  I also like the use of "swirling" on the background and the webpage.  I hope this additional information is helpful.

Requirements
Must have
• I need a place to insert "client testimonials", a place to insert four logos of awards the law firm has received, a place for people to fill out a form to contact the law firm via email, and a place for people to click to review articles I have written.

```html
<!DOCTYPE html>
<html lang="en">
<head>
<meta charset="utf-8">
<title>Alderwick Law</title>
<link href="https://fonts.googleapis.com/css2?family=PT+Sans:wght@400;700&family=Arimo:wght@400;700&display=swap" rel="stylesheet">
<style>
:root{
  --bg:#dfe2f1;
  --tan:#deb07c;
  --tan-light:#e8c293;
  --tan-dark:#cf9c66;
  --gold-light:#e8c76b;
  --brown:#8a6a3a;
  --ink:#1f1f1f;
  --card:#f1f1f1;
  --text:#444444;
  --dark:#262626;
  --paper:radial-gradient(ellipse at 30% 20%,var(--tan-light) 0%,var(--tan) 55%,var(--tan-dark) 100%);
}
*{margin:0;padding:0;box-sizing:border-box}
html,body{width:758px;height:1200px;overflow:hidden}
body{position:relative;background:var(--bg);font-family:"Arimo",Arial,sans-serif;color:var(--text)}
.abs{position:absolute}

.header-band{left:83px;top:0;width:593px;height:85px;background:linear-gradient(180deg,#eef0f8,#dfe2f1)}
.swirl{left:83px;top:0}
.logo-card{left:83px;top:15px;width:240px;height:66px;background:#fff;border-radius:0 14px 0 0;box-shadow:0 2px 5px rgba(0,0,0,.25);display:flex;align-items:center;padding-left:12px;gap:12px}
.logo-mark{width:40px;height:40px;background:var(--ink)}
.logo-name{font-family:"PT Sans",Arial,sans-serif;font-size:23px;color:#8f7636;line-height:1}
.phone{left:488px;top:20px;font-family:"PT Sans",Arial,sans-serif;color:var(--ink);font-size:12.5px;line-height:20px}
.phone b{font-size:18px;font-weight:400;margin-left:4px}

.nav a{position:absolute;top:60px;height:25px;background:linear-gradient(180deg,#d8b75a,#a7812c);border-radius:8px 8px 0 0;color:#2a2210;font:700 9.5px "Arimo",Arial,sans-serif;display:flex;align-items:center;justify-content:center;text-decoration:none;box-shadow:0 -1px 2px rgba(0,0,0,.2)}
.nav a.current{color:#fff}

.hero{left:83px;top:85px;width:593px;height:257px;border:2px solid #fff;background:linear-gradient(180deg,#a9cbe8,#b9c78e);box-shadow:0 2px 6px rgba(0,0,0,.3)}
.hero-band{left:0;top:193px;width:589px;height:34px;background:rgba(255,255,255,.5)}
.hero-title{left:17px;top:195px;font:400 26px/30px "PT Sans",Arial,sans-serif;color:#1d1d1d}
.hero-btn{left:400px;top:198px;width:175px;height:23px;border-radius:6px;background:linear-gradient(180deg,#f0b768,#c97a2a);border:1px solid #a8651f;font:400 14px "PT Sans",Arial,sans-serif;color:#2a1a08;display:flex;align-items:center;justify-content:center}

.slide-strip{left:83px;top:342px;width:400px;height:28px;background:var(--paper);border-radius:0 0 0 20px}
.pager{left:149px;top:350px;display:flex;gap:5px}
.pager span{width:17px;height:15px;background:#fff;border-radius:3px;font:700 11px "Arimo",Arial,sans-serif;display:flex;align-items:center;justify-content:center;color:#222}
.pager span.on{background:#2a2a2a;color:#fff}

.panel{left:83px;width:391px;background:var(--card);border-radius:14px;box-shadow:0 2px 4px rgba(0,0,0,.25);padding:9px 10px}
.panel h2{font:400 18px/22px "PT Sans",Arial,sans-serif;color:var(--brown);margin-bottom:1px}
.panel p{font-size:7.9px;line-height:11.3px;color:var(--text)}

.sidebar{left:486px;top:358px;width:190px;height:818px;background:var(--paper);border-radius:14px 4px 14px 14px;box-shadow:0 2px 5px rgba(0,0,0,.25)}
.tab{height:24px;background:linear-gradient(180deg,#2a2a2a,#111);color:#fff;font:400 15px "PT Sans",Arial,sans-serif;display:flex;align-items:center;padding-left:14px;border-radius:0 8px 0 0;box-shadow:2px 3px 3px rgba(0,0,0,.35)}
.practice{left:513px;top:401px;list-style:none}
.practice li{font-size:8.4px;height:15.9px;line-height:12px;color:#222}
.practice li::before{content:"»";display:inline-block;width:21px;font-weight:700}
.side-text{left:503px;width:162px;font-size:8.2px;line-height:11px;color:#222}
.side-art{border-radius:6px}
.click-btn{left:617px;width:51px;height:16px;background:#fff;border-radius:3px;font:700 8.5px "Arimo",Arial,sans-serif;color:#222;display:flex;align-items:center;justify-content:center;box-shadow:0 1px 2px rgba(0,0,0,.3)}

.box-tan{top:780px;height:215px;background:var(--paper);border-radius:12px;box-shadow:0 2px 4px rgba(0,0,0,.25)}
.badge{background:#fff;border:1px solid #bbb}
.contact-copy{left:342px;top:815px;width:125px;font-size:8px;line-height:11px;color:#222}
.field{left:342px;width:117px;height:16px;background:#fff;border:1px solid #b58a5a;font-size:7.5px;color:#666;padding:3px 5px}
.submit{left:408px;top:974px;width:52px;height:16px;background:linear-gradient(180deg,#d7b35d,#a47d2d);border-radius:3px;color:#fff;font:700 10px "Arimo",Arial,sans-serif;display:flex;align-items:center;justify-content:center}

.testimonials{left:83px;top:1007px;width:391px;height:200px;background:var(--dark);border-radius:12px 12px 0 0}
.tab-tan{background:var(--paper);color:#111}
.quote-mark{left:95px;top:1038px;font:700 44px Georgia,serif;color:#777;line-height:1}
.quote{left:123px;top:1053px;width:320px;font-size:8.3px;line-height:12px;color:#ddd}
.more{left:123px;top:1091px;font-size:8.5px;color:#fff;text-decoration:underline;font-style:italic}
.by{left:380px;top:1089px;width:80px;text-align:right;font:700 8.5px "Arimo",Arial,sans-serif;color:#fff;line-height:12px}
.rule{left:83px;width:391px;height:1px;background:#444}
.footer-links{left:137px;top:1125px;font-size:7.5px;color:var(--gold-light)}
.footer-links span{color:#888;margin:0 4px}
.copy{left:90px;top:1150px;font-size:7px;line-height:11px;color:#ccc}
.accept{left:233px;top:1150px;font-size:9px;color:#fff}
.cards{left:233px;top:1165px;display:flex;gap:2px}
.cards span{width:31px;height:20px;background:#e9e9e9;border-radius:2px;font:700 5.5px "Arimo",Arial,sans-serif;color:#333;display:flex;align-items:center;justify-content:center}
.social-label{left:400px;top:1150px;font-size:9px;color:#fff}
.social{left:398px;top:1168px;display:flex;gap:6px;font-size:7px;color:#888}
</style>
</head>
<body>

<div class="abs header-band"></div>
<svg class="abs swirl" width="593" height="90" viewBox="0 0 593 90" aria-hidden="true">
  <path d="M0 0 H10 Q100 5 250 55 Q300 75 330 80 L0 80 Z" fill="#deb07c"/>
  <path d="M180 0 Q240 20 300 55 Q330 75 380 70" fill="none" stroke="#c9955f" stroke-width="1.2"/>
</svg>

<div class="abs logo-card">
  <div class="logo-mark"></div>
  <div class="logo-name">Alderwick Law</div>
</div>

<div class="abs phone">Call Us Today: <b>123-456 7890</b></div>

<nav class="nav">
  <a class="current" style="left:356px;width:55px">HOME</a>
  <a style="left:416px;width:118px">MEET OUR ATTORNEY</a>
  <a style="left:540px;width:48px">FAQ</a>
  <a style="left:594px;width:82px">CONTACT US</a>
</nav>

<div class="abs slide-strip"></div>

<div class="abs hero" role="img" aria-label="Photo of a family walking through a sunny meadow">
  <div class="abs hero-band"></div>
  <div class="abs hero-title">PROBLEM HIRE US !</div>
  <div class="abs hero-btn">Request a Consultation</div>
</div>

<div class="abs pager"><span class="on">1</span><span>2</span><span>3</span><span>4</span></div>

<section class="abs panel" style="top:381px;height:122px">
  <h2>Welcome to Alderwick Law</h2>
  <p>Lorem ipsum dolor amet conse ctetur adipisicing elit, sed do eiusmod tempor incididunt ut labore et dolore magna aliqua. Ut enim ad minim veniam, quis nostrud exercitation ullamco laboris nisi ut aliquip.</p>
  <p>Dolor amet conse ctetur adipisicing elit, sed do eiusmod tempor incididunt ut labore et dolore magna aliqua. Ut enim ad minim veniam, quis nostrud exercitation ullamco laboris nisi ut aliquip ex ea commodo consequat ut enim ad.</p>
</section>
<section class="abs panel" style="top:514px;height:121px">
  <h2>Uncontested Divorce</h2>
  <p>Lorem ipsum dolor amet conse ctetur adipisicing elit, sed do eiusmod tempor incididunt ut labore et dolore magna aliqua. Ut enim ad minim veniam, quis nostrud exercitation ullamco laboris nisi ut aliquip.</p>
  <p>Dolor amet conse ctetur adipisicing elit, sed do eiusmod tempor incididunt ut labore et dolore magna aliqua. Ut enim ad minim veniam, quis nostrud exercitation ullamco laboris nisi ut aliquip ex ea commodo consequat ut enim ad.</p>
</section>
<section class="abs panel" style="top:647px;height:121px">
  <h2>Alderwick Divorce Attorney</h2>
  <p>Lorem ipsum dolor amet conse ctetur adipisicing elit, sed do eiusmod tempor incididunt ut labore et dolore magna aliqua. Ut enim ad minim veniam, quis nostrud exercitation ullamco laboris nisi ut aliquip.</p>
  <p>Dolor amet conse ctetur adipisicing elit, sed do eiusmod tempor incididunt ut labore et dolore magna aliqua. Ut enim ad minim veniam, quis nostrud exercitation ullamco laboris nisi ut aliquip ex ea commodo consequat ut enim ad.</p>
</section>

<aside class="abs sidebar"></aside>
<div class="abs tab" style="left:502px;top:370px;width:180px">Area of Practice</div>
<ul class="abs practice">
  <li>Family Law</li><li>Divorce</li><li>Alimony</li><li>Child Custody</li><li>Child Support</li>
  <li>Collaborative Divorce</li><li>Contested Divorce</li><li>Division of Assets</li><li>Domestic Violence</li>
  <li>Family/Relative Adoption</li><li>Fathers' Rights</li><li>Grandparents' Rights</li><li>Guardianship</li>
  <li>Legal Separation</li><li>Mediation</li><li>Modification of Spousal Support</li><li>Mothers' Rights</li>
  <li>Palimony</li><li>Parental Alienation</li><li>Paternity</li><li>Prenuptial Agreements</li>
  <li>Postnuptial Agreements</li><li>Property Division</li><li>Relocation</li><li>Uncontested Divorce</li><li>Visitation</li>
</ul>

<div class="abs tab" style="left:502px;top:816px;width:180px">Video Center</div>
<p class="abs side-text" style="top:845px">Need more information? Learn more about your case from your informative videos.</p>
<div class="abs side-art" style="left:526px;top:880px;width:48px;height:48px;background:linear-gradient(160deg,#cfe3f7,#3b6fc2)" role="img" aria-label="Illustration of a computer monitor"></div>
<div class="abs click-btn" style="top:909px">Click Here</div>

<div class="abs tab" style="left:502px;top:934px;width:180px">Click to Call</div>
<p class="abs side-text" style="top:962px">Have a question about your case? Click here to connect to our office.</p>
<svg class="abs" style="left:535px;top:993px" width="32" height="56" viewBox="0 0 32 56" aria-label="Mobile phone icon" role="img">
  <rect x="3" y="2" width="26" height="52" rx="5" fill="#555"/>
  <rect x="7" y="8" width="18" height="22" fill="#cfd6dc"/>
  <circle cx="16" cy="42" r="4" fill="#888"/>
</svg>
<div class="abs click-btn" style="top:1033px">Click Here</div>

<div class="abs tab" style="left:502px;top:1058px;width:180px">Case Evaluation</div>
<p class="abs side-text" style="top:1087px">Fill out our online case evaluation form to receive a free consultation</p>
<div class="abs side-art" style="left:530px;top:1115px;width:44px;height:42px;background:linear-gradient(150deg,#fff,#f2c9a0)" role="img" aria-label="Illustration of a pencil writing on a form"></div>
<div class="abs click-btn" style="top:1138px">Click Here</div>

<section class="abs box-tan" style="left:83px;width:239px"></section>
<div class="abs tab" style="left:77px;top:788px;width:179px">Our Achievements</div>
<div class="abs badge" style="left:92px;top:827px;width:142px;height:68px"></div>
<div class="abs badge" style="left:92px;top:900px;width:142px;height:67px"></div>
<div class="abs badge" style="left:239px;top:827px;width:72px;height:140px"></div>

<section class="abs box-tan" style="left:334px;width:139px"></section>
<div class="abs tab" style="left:329px;top:788px;width:131px">Contact Us</div>
<p class="abs contact-copy">Send us a quick email with any questions or concerns you may have about your potential case.</p>
<div class="abs field" style="top:856px">Name</div>
<div class="abs field" style="top:876px">Phone</div>
<div class="abs field" style="top:897px">Email</div>
<div class="abs field" style="top:917px;height:53px">Tell us about your case</div>
<div class="abs submit">Submit</div>

<section class="abs testimonials"></section>
<div class="abs tab tab-tan" style="left:77px;top:1017px;width:179px">Client Testimonials</div>
<div class="abs quote-mark">&ldquo;</div>
<p class="abs quote">In pulvinar nulla. Sed tempus iaculis mauris at laoreet. Sed nisl diam, rutrum ut viverra non, eleifend quis odio. Sed in feugiat orci. Vivamus sem erat, tempus sed posuere sit amet, sodales. venenatis turpis.........</p>
<a class="abs more">Continue Reading</a>
<div class="abs by">By<br>Marek Lindqvist</div>
<div class="abs rule" style="top:1118px"></div>
<div class="abs footer-links">Alderwick Divorce Attorney<span>|</span>Contact Us<span>|</span>Resources<span>|</span>Privacy Policy<span>|</span>Site Map</div>
<div class="abs rule" style="top:1140px"></div>
<div class="abs copy">© 2012 by Alderwick Law<br>All Rights Reserved / Privacy Policy</div>
<div class="abs accept">We Proudly Accept</div>
<div class="abs cards"><span>Amberpay</span><span>Tollcard</span><span>Merit</span><span>Ridgepay</span></div>
<div class="abs social-label">We are also on</div>
<div class="abs social"><span>Chirp</span><span>Folio</span><span>Linkr</span></div>

</body>
</html>
```